Marcus Delbridge Finance

Need a personal website advertising Equipment Finance,Business Finance,Commercial Finance, Construction Finance, Bridging Finance. Similar websites are www.corvalend.com.au / www.tarmivest.com.au / www.qbr7.com.au /wwwhalvecredit.com.au

Target Market(s)

Business People

Industry/Entity Type

Business

Number of Pages Required

3 page

Font styles to use
Serif
Sans Serif

Requirements
Must have
• All i want is a simple corporate looking website advertising Equipment Finance, Commercial Finance, Construction Finance, Business Finance, Bridging Finance,

```html
<!DOCTYPE html>
<html lang="en">
<head>
<meta charset="utf-8">
<title>Marcus Delbridge Finance</title>
<link href="https://fonts.googleapis.com/css2?family=Open+Sans:wght@400;600;700&family=Raleway:wght@400;600&display=swap" rel="stylesheet">
<style>
:root{
  --blue:#1a86c8;
  --blue-dark:#0f6aa6;
  --blue-deep:#0b5288;
  --ink:#333a40;
  --muted:#7b8590;
  --line:#d5dbe0;
  --white:#ffffff;
  --hero-a:#5d6c78;
  --hero-b:#2c3a46;
}
*{box-sizing:border-box;margin:0;padding:0}
html,body{width:1200px;height:2772px;overflow:hidden;background:var(--white)}
body{font-family:"Open Sans",Arial,sans-serif;color:var(--ink);position:relative}
.topbar{position:absolute;left:0;top:0;width:1200px;height:32px;background:var(--blue);color:var(--white);font-size:12px;display:flex;align-items:center;justify-content:space-between;padding:0 100px}
.topbar .social{display:flex;gap:8px}
.topbar .social span{width:12px;height:12px;border-radius:2px;background:rgba(255,255,255,.85)}
.header{position:absolute;top:32px;left:0;width:1200px;height:128px;background:var(--white)}
.brand{position:absolute;left:100px;top:50px;display:flex;align-items:center;gap:12px}
.brand-mark{width:26px;height:26px;background:var(--blue)}
.brand-name{font-weight:700;font-size:20px;color:var(--blue-dark);letter-spacing:.5px}
.nav{position:absolute;right:100px;top:50px;display:flex;gap:4px}
.nav a{font-size:13px;font-weight:600;color:var(--ink);text-decoration:none;padding:8px 14px}
.nav a.active{background:var(--blue);color:var(--white)}
.hero{position:absolute;top:160px;left:0;width:1200px;height:620px;background:linear-gradient(160deg,var(--hero-a),var(--hero-b) 60%,#1f4466)}
.hero-curve{position:absolute;left:0;bottom:0}
.hero h1{position:absolute;top:180px;width:100%;text-align:center;font-size:62px;font-weight:700;color:var(--white);letter-spacing:1px}
.hero p{position:absolute;top:270px;width:100%;text-align:center;font-size:17px;color:var(--white)}
.hero .btn{position:absolute;left:506px;top:340px;width:188px;height:40px;background:var(--blue);color:var(--white);font-size:14px;display:flex;align-items:center;justify-content:center;border-radius:3px}
.hero .arrow{position:absolute;top:240px;color:rgba(255,255,255,.7);font-size:40px}
.section-title{position:absolute;width:100%;text-align:center;font-family:"Raleway",sans-serif;font-size:30px;font-weight:600;letter-spacing:1px;color:var(--ink)}
.services{position:absolute;left:100px;top:876px;width:1000px;display:grid;grid-template-columns:repeat(3,316px);gap:26px 26px}
.card{height:288px;display:flex;flex-direction:column;border:1px solid var(--line)}
.card .photo{flex:1}
.card .label{height:58px;background:var(--blue);color:var(--white);font-size:17px;font-weight:600;display:flex;align-items:center;justify-content:center;letter-spacing:.5px}
.p1{background:linear-gradient(135deg,#c9b08c,#7f8a6a)}
.p2{background:linear-gradient(135deg,#cfe0ee,#6f9ec4)}
.p3{background:linear-gradient(135deg,#bcd2e4,#4e7ea6)}
.p4{background:linear-gradient(135deg,#a67d52,#4b5860)}
.p5{background:linear-gradient(135deg,#dfe4ea,#8d9aa8)}
.promo{position:absolute;top:1592px;left:0;width:1200px;height:396px;background:linear-gradient(120deg,#1e90d3,var(--blue-deep))}
.promo .photo{position:absolute;left:0;top:0;width:560px;height:396px;background:linear-gradient(180deg,#d4e6f4,#6e97b8 60%,#2f5f86)}
.promo-text{position:absolute;left:700px;top:56px;width:380px;color:var(--white)}
.promo-text h2{font-family:"Raleway",sans-serif;font-weight:400;font-size:38px;line-height:1.25}
.promo-text p{margin-top:22px;font-size:13px;line-height:1.7;opacity:.9}
.form{position:absolute;left:100px;top:2206px;width:1000px}
.form .row{display:grid;grid-template-columns:repeat(3,316px);gap:26px}
.field{height:32px;border:1px solid var(--line);font-size:12px;color:var(--muted);padding:0 10px;display:flex;align-items:center}
.field.msg{margin-top:26px;height:80px;align-items:flex-start;padding-top:10px}
.submit{margin-top:24px;width:160px;height:40px;border-radius:22px;background:var(--blue);color:var(--white);font-weight:700;font-size:14px;display:flex;align-items:center;justify-content:center}
.footer{position:absolute;top:2428px;left:0;width:1200px;height:292px;background:var(--blue);color:var(--white)}
.col{position:absolute;top:60px;font-size:12px;line-height:22px}
.col h4{font-size:15px;font-weight:600;letter-spacing:.5px;margin-bottom:12px}
.col li{list-style:none;opacity:.9}
.circles{display:flex;gap:8px;margin-top:8px}
.circles span{width:30px;height:30px;border-radius:50%;background:rgba(255,255,255,.9)}
.bottombar{position:absolute;top:2720px;left:0;width:1200px;height:52px;background:var(--blue-dark);color:var(--white);font-size:12px;display:flex;align-items:center;justify-content:space-between;padding:0 100px}
</style>
</head>
<body>
<div class="topbar"><span>Call us: +61 7 5550 1234 &nbsp;|&nbsp; Email: info@delbridgefinance.com.au</span><div class="social"><span></span><span></span><span></span><span></span><span></span></div></div>
<header class="header">
  <div class="brand"><span class="brand-mark"></span><span class="brand-name">MARCUS DELBRIDGE</span></div>
  <nav class="nav"><a class="active">HOME</a><a>ABOUT US</a><a>THE BUSINESS</a><a>INVESTORS</a><a>BLOG</a><a>CONTACT US</a></nav>
</header>
<section class="hero" role="img" aria-label="Businessman's hand touching a glowing financial chart over a city skyline">
  <span class="arrow" style="left:22px">‹</span><span class="arrow" style="right:22px">›</span>
  <h1>Marcus Delbridge Finance</h1>
  <p>We provide Equipment Finance, Business Finance, Commercial Finance, Construction Finance, Bridging Finance</p>
  <div class="btn">Click More Details »</div>
  <svg class="hero-curve" width="1200" height="70" viewBox="0 0 1200 70"><path d="M0 70 L0 10 Q600 90 1200 10 L1200 70 Z" fill="#ffffff"/></svg>
</section>
<h2 class="section-title" style="top:800px">WHAT WE PROVIDE</h2>
<section class="services">
  <div class="card"><div class="photo p1" role="img" aria-label="Team of business people outdoors"></div><div class="label">EQUIPMENT FINANCE</div></div>
  <div class="card"><div class="photo p2" role="img" aria-label="Business handshake"></div><div class="label">BUSINESS FINANCE</div></div>
  <div class="card"><div class="photo p3" role="img" aria-label="Glass office towers"></div><div class="label">COMMERCIAL FINANCE</div></div>
  <div class="card"><div class="photo p4" role="img" aria-label="Construction worker in hard hat beside a truck"></div><div class="label">CONSTRUCTION FINANCE</div></div>
  <div class="card"><div class="photo p5" role="img" aria-label="Business professionals in an office meeting"></div><div class="label">BRIDGING FINANCE</div></div>
</section>
<section class="promo">
  <div class="photo" role="img" aria-label="Skyscrapers seen from below with a dollar sign reflected in the glass"></div>
  <div class="promo-text">
    <h2>Easy Commercial Finance! Fast Approvals</h2>
    <p>We work with businesses of every size to arrange fast, flexible funding for equipment, property and growth. Our team compares lenders, handles the paperwork and keeps you informed from first call to settlement, so approvals arrive quickly and without fuss.</p>
  </div>
</section>
<h2 class="section-title" style="top:2140px">QUICK CONTACT</h2>
<form class="form">
  <div class="row"><div class="field">Name</div><div class="field">Email Address</div><div class="field">Phone Number</div></div>
  <div class="field msg">Your Message</div>
  <div class="submit">SUBMIT NOW</div>
</form>
<footer class="footer">
  <div class="col" style="left:100px"><h4>COMPANY</h4><ul><li>Home</li><li>About Us</li><li>The Business</li><li>Blog</li><li>Contact</li></ul></div>
  <div class="col" style="left:252px"><h4>SERVICES</h4><ul><li>Equipment Finance</li><li>Business Finance</li><li>Commercial Finance</li><li>Construction Finance</li><li>Bridging Finance</li></ul></div>
  <div class="col" style="left:452px"><h4>GET IN TOUCH</h4><ul><li>☎ Call us on +61 7 5550 1234</li><li>✉ info@delbridgefinance.com.au</li><li>⚲ Unit 14 Harbour Lane</li><li>&nbsp;&nbsp;&nbsp;Coral Bay, Queensland 4000</li></ul></div>
  <div class="col" style="left:760px"><h4>WHY US</h4><ul><li>My Account</li><li>Team</li><li>Privacy &amp; Policy</li><li>FAQ</li></ul></div>
  <div class="col" style="left:928px"><h4>FOLLOW US</h4><ul><li>Please connect with us on</li></ul><div class="circles"><span></span><span></span><span></span><span></span></div></div>
</footer>
<div class="bottombar"><span>© 2015 Marcus Delbridge. All rights reserved. Terms of Use</span><span>Top</span></div>
</body>
</html>
```